Website for Dental Office - The Bright Arch Clinic

The bright arch clinic is a dental office offering cosmetic dentistry, general dentistry, and multi-specialty dental care all under one roof in our state-of-the-art cosmetic dental center. We are particularly striving to provide services that fit the need of the young generation. Thus, we hope to have a modern, professional concise website that represents our spirit.

*Should be able to switch from English to Chinese

6 sections besides homepage:
Home, Meet us, Services,
Patient Info, Cases&Reviews, Blog, Contact

The Services sections should contain multiple subsections such as cleaning and prevention, cosmetic dentistry, implant dentistry, removable dentures, etc...
The Patient Info section is also intended to contain several subsections such as
New Patient offer, accepted Insurance, patient portal, helpful tips, etc...

Target Market(s)

young generation

Coding

Coded - Design and coding required

Number of Pages Required

5+ page

Font styles to use
Sans Serif

Colors
0592cd
33a6d7
85cae6
00a990
33b8a4
86cfc6
cee9f5
cfeae6
3277b5

Requirements
Must have
• *Should be able to switch from English to Chinese
Nice to have
• http://www.thebrightarchclinic.com/
• As a reference, the above link is the current website, but we would like to change the appearance and the content (our new logo's picture is attached)

```html
<!DOCTYPE html>
<html lang="en">
<head>
<meta charset="utf-8">
<title>Accepted Insurance – The Bright Arch Clinic</title>
<link href="https://fonts.googleapis.com/css2?family=Montserrat:wght@400;500;600;700&display=swap" rel="stylesheet">
<style>
:root{
  --blue-deep:#0592cd;
  --blue:#33a6d7;
  --blue-soft:#85cae6;
  --blue-pale:#d9f0fb;
  --navy:#3277b5;
  --green:#00a990;
  --green-mid:#33b8a4;
  --ink:#111;
  --text:#555;
  --grey-bg:#f1f1f1;
  --grey-bar:#e8e8e8;
}
*{margin:0;padding:0;box-sizing:border-box}
html,body{width:1200px;height:1132px;overflow:hidden}
body{font-family:"Montserrat",sans-serif;color:var(--text);background:#fff;position:relative}
.page{position:absolute;inset:0;background:linear-gradient(var(--blue-pale) 0,var(--blue-pale) 150px,#fff 620px)}
.footer-zone{position:absolute;left:0;right:0;top:766px;bottom:0;background:var(--grey-bg)}
.abs{position:absolute}
.top-rule{position:absolute;left:0;right:0;top:0;height:2px;background:var(--navy)}
.arc{position:absolute;left:0;top:0}
.brand{left:161px;top:20px;display:flex;align-items:center;gap:10px;font-weight:700;font-size:17px;line-height:21px;color:var(--blue);text-transform:uppercase;width:225px}
.brand .brand-dot{flex:none;width:40px;height:40px}
.brand-dot{border-radius:50%;background:var(--blue)}
.nav{left:398px;top:38px;display:flex;gap:0;font-size:10.5px;font-weight:500;color:#555;text-transform:uppercase}
.nav span{margin-right:18.5px}
.nav .active{color:var(--green)}
.call{left:865px;top:-21px;width:112px;height:117px;border-radius:50%;background:var(--navy);color:#fff;text-align:center;font-weight:700;font-size:13px}
.call svg{margin-top:36px}
.call div{margin-top:4px}
.lang{left:988px;top:29px;width:51px;height:30px;border-radius:3px;background:var(--green);color:#fff;font-size:10px;display:flex;align-items:center;justify-content:center;gap:5px}
.title{left:0;right:0;top:214px;text-align:center;font-size:42px;font-weight:700;color:var(--ink);letter-spacing:.5px}
.lead{left:335px;width:530px;top:277px;text-align:center;font-size:11px;line-height:19.5px}
.tick{left:381px;top:380px}
.subhead{left:443px;top:371px;width:420px;font-size:25px;line-height:33px;font-weight:700;color:var(--ink)}
.body{font-size:11px;line-height:19.5px}
.col-a{left:163px;top:467px;width:395px}
.col-b{left:601px;top:467px;width:395px}
.wide{left:163px;top:572px;width:875px}
.banner{left:0;top:0}
.cta-small{left:183px;top:741px;font-size:11.5px;color:#fff}
.cta-big{left:183px;top:757px;font-size:36px;font-weight:700;color:#fff;letter-spacing:.5px}
.cta-btn{left:783px;top:764px;width:225px;height:44px;border-radius:22px;background:#fff;color:#222;font-size:12.5px;font-weight:600;display:flex;align-items:center;justify-content:center;letter-spacing:.3px}
.foot-brand{left:161px;top:896px;width:195px;text-align:center}
.foot-brand .brand-dot{width:64px;height:64px;margin:0 auto 14px}
.foot-brand p{font-weight:700;font-size:16px;line-height:20px;color:var(--blue)}
.socials{left:180px;top:1010px;display:flex;gap:7px}
.socials span{width:34px;height:34px;border-radius:50%}
.fh{font-size:11.5px;font-weight:600;color:#333;letter-spacing:.5px}
.list{font-size:10.5px;line-height:18.75px;color:#555}
.hours-time{font-weight:700;color:#444}
.contact-row{display:flex;gap:12px;align-items:flex-start}
.bottom{left:0;right:0;top:1087px;height:45px;background:var(--grey-bar);font-size:11px;color:#888}
.bottom .l{position:absolute;left:163px;top:15px}
.bottom .r{position:absolute;right:162px;top:15px;color:var(--green)}
.bottom a{color:var(--navy);text-decoration:none}
</style>
</head>
<body>
<div class="page"></div>
<div class="footer-zone"></div>

<svg class="arc" width="1200" height="240" viewBox="0 0 1200 240" aria-hidden="true">
  <path d="M0 0H1200V68Q600 236 0 68Z" fill="#fff"/>
</svg>
<div class="top-rule"></div>

<header>
  <div class="abs brand"><span class="brand-dot"></span><span>The Bright<br>Arch Clinic</span></div>
  <nav class="abs nav">
    <span>Home</span><span>Meet Us</span><span>Services</span><span class="active">Patient Info</span><span>Reviews</span><span>Blog</span><span>Contact</span>
  </nav>
  <div class="abs call">
    <svg width="24" height="24" viewBox="0 0 24 24"><path d="M6.6 10.8c1.4 2.8 3.8 5.2 6.6 6.6l2.2-2.2c.3-.3.7-.4 1-.2 1.1.4 2.3.6 3.6.6.6 0 1 .4 1 1V20c0 .6-.4 1-1 1C10.6 21 3 13.4 3 4c0-.6.4-1 1-1h3.5c.6 0 1 .4 1 1 0 1.3.2 2.5.6 3.6.1.3 0 .7-.2 1z" fill="#fff"/></svg>
    <div>555.204.7180</div>
  </div>
  <div class="abs lang">汉语
    <svg width="9" height="6" viewBox="0 0 9 6"><path d="M1 1l3.5 3.5L8 1" stroke="#fff" stroke-width="1.6" fill="none"/></svg>
  </div>
</header>

<main>
  <h1 class="abs title">ACCEPTED INSURANCE</h1>
  <p class="abs lead">Lorem Ipsum is dummy text of the printing and typesetting industry. Lorem Ipsum has been the industry's standard dummy text.</p>

  <svg class="abs tick" width="50" height="40" viewBox="0 0 50 40" aria-hidden="true">
    <path d="M4 22l11 13L46 5" stroke="var(--navy)" stroke-width="5" fill="none" stroke-linecap="round" stroke-linejoin="round"/>
    <path d="M4 22l11 13L46 5" stroke="#fff" stroke-width="1.6" fill="none" stroke-linecap="round" stroke-linejoin="round"/>
  </svg>
  <h2 class="abs subhead">Lorem Ipsum is dummy text of the printing</h2>

  <p class="abs body col-a">Lorem Ipsum is simply dummy text of the printing and typesetting industry. Lorem Ipsum has been the industry's standard dummy text ever since the 1500s, when an unknown printer took a galley of type and scrambled it to make a type specimen book.</p>
  <p class="abs body col-b">Lorem Ipsum is simply dummy text of the printing and typesetting industry. Lorem Ipsum has been the industry's standard dummy text ever since the 1500s, when an unknown printer took a galley of type and scrambled it to make a type specimen book.</p>
  <p class="abs body wide">Lorem Ipsum is simply dummy text of the printing and typesetting industry. Lorem Ipsum has been the industry's standard dummy text ever since the 1500s, when an unknown printer took a galley of type and scrambled it to make a type specimen book.</p>

  <section>
    <svg class="abs banner" width="1200" height="860" viewBox="0 0 1200 860" aria-hidden="true">
      <defs>
        <linearGradient id="ctaGrad" x1="0" x2="1" y1="0" y2="0">
          <stop offset="0" stop-color="#0592cd"/>
          <stop offset="1" stop-color="#00a990"/>
        </linearGradient>
      </defs>
      <path d="M161 690Q161 684 167 684L1033 728Q1039 729 1039 735V844Q1039 850 1033 850H167Q161 850 161 844Z" fill="url(#ctaGrad)"/>
    </svg>
    <p class="abs cta-small">Lorem Ipsum is dummy text of the printing and typesetting.</p>
    <p class="abs cta-big">YOUR SMILE. OUR PASSION.</p>
    <div class="abs cta-btn">BOOK AN APPOINTMENT</div>
  </section>
</main>

<footer>
  <div class="abs foot-brand"><div class="brand-dot"></div><p>The Bright Arch Clinic</p></div>
  <div class="abs socials">
    <span style="background:var(--blue)"></span><span style="background:var(--navy)"></span><span style="background:var(--green)"></span><span style="background:var(--green-mid)"></span>
  </div>

  <div class="abs" style="left:390px;top:892px">
    <p class="fh">USEFUL LINKS</p>
    <div class="list" style="margin-top:9px">Home<br>Meet Us<br>Services<br>Patient Info<br>Case &amp; Reviews<br>Blog<br>Contact</div>
  </div>

  <div class="abs" style="left:617px;top:892px">
    <p class="fh">OPENING HOURS</p>
    <div style="display:flex;gap:9px;margin-top:9px">
      <div class="list">Sunday &amp; Monday<br>Tuesday<br>Wednesday<br>Thursday<br>Friday<br>Saturday</div>
      <div class="list hours-time">Closed<br>9:30AM – 5:00PM<br>Closed<br>9:30AM – 5:00PM<br>9:00AM – 5:00PM<br>9:00AM – 5:00PM</div>
    </div>
  </div>

  <div class="abs" style="left:846px;top:892px;width:200px">
    <p class="fh">CONTACT INFO</p>
    <div class="contact-row" style="margin-top:9px">
      <svg width="11" height="15" viewBox="0 0 11 15" style="margin-top:3px"><path d="M5.5 0A5.5 5.5 0 0 0 0 5.5C0 9.6 5.5 15 5.5 15S11 9.6 11 5.5A5.5 5.5 0 0 0 5.5 0zm0 7.6a2.1 2.1 0 1 1 0-4.2 2.1 2.1 0 0 1 0 4.2z" fill="var(--green)"/></svg>
      <div class="list">270 Linden Avenue, Suite 12,<br>Fairmont MA 02190</div>
    </div>
    <div class="contact-row" style="margin-top:11px;align-items:center">
      <svg width="14" height="14" viewBox="0 0 24 24"><path d="M6.6 10.8c1.4 2.8 3.8 5.2 6.6 6.6l2.2-2.2c.3-.3.7-.4 1-.2 1.1.4 2.3.6 3.6.6.6 0 1 .4 1 1V20c0 .6-.4 1-1 1C10.6 21 3 13.4 3 4c0-.6.4-1 1-1h3.5c.6 0 1 .4 1 1 0 1.3.2 2.5.6 3.6.1.3 0 .7-.2 1z" fill="var(--navy)"/></svg>
      <div style="font-size:14px;color:#555;font-weight:500">555.204.7180</div>
    </div>
    <div class="contact-row" style="margin-top:14px;align-items:center">
      <svg width="14" height="11" viewBox="0 0 14 11"><rect width="14" height="11" rx="1" fill="var(--blue)"/><path d="M1 1.5l6 4.5 6-4.5" stroke="#fff" stroke-width="1.2" fill="none"/></svg>
      <div class="list">info@thebrightarchclinic.com</div>
    </div>
  </div>

  <div class="abs bottom">
    <span class="l">© <a href="http://www.thebrightarchclinic.com/">The Bright Arch Clinic</a> – 2019. All Rights Reserved.</span>
    <span class="r">Harbor Skin and Filler Studio</span>
  </div>
</footer>
</body>
</html>
```